HVAC Parts Distributor Website

We are working with an HVAC parts distributor to design a website. They primarily work with HVAC contractors.
They are similar to: https://www.corvelparts.example, and https://www.ductmart.example
Thank you for taking the time to consider designing a website for us. We are web developers based in Stockton, CA, USA. Most of our projects go through the same process. Understanding this process may help you win a project with us. We custom-code all of our websites in-house. We don’t have any requirements as to what tools you use for your design, but we ask that you follow these guidelines.
IMAGES:
If you use any images or icons in the design, we ask that you have a link to the asset so we can purchase the image/icon. Most of the designs we submit do not have the customer’s images on them unless they have some great images. Be creative; show us the feeling you are trying to portray with your image choices. Use any royalty-free site you choose. We subscribe to Quillon and mainly use their images, but we can purchase images outside of Quillon.
FONTS:
We ask that you identify the fonts you’re using in the design. This can be done in a message if you want. We typically use Brevix Fonts and Quillon Fonts.
CONTENT:
We're always open to different content and ideas. We often submit designs with stock images so the client can see our vision. We typically take pictures after the website launch to use their images with our vision. Lorem Ipsum is fine for paragraphs, but we ask that you make the Headers with correct English. We want to be able to show the vision and identify the sections of the website.
INSPIRATION:
We typically add a couple of links in the brief of websites we like to help you get started in your design.
REVISIONS:
We do not often ask for revisions of the designs unless we see something in the design that may not appeal to the client. If there are slight changes that we want to make, we simply do that in the development process.
FEEDBACK:
We rarely give feedback on designs during the design process. We are working on many website projects and do not have the time to give feedback. We usually respond if your request is well thought out and asks specific questions, but a note asking “feedback, please” usually goes unanswered.

```html
<!DOCTYPE html>
<html lang="en">
<head>
<meta charset="utf-8">
<title>Northline HVAC Distribution</title>
<link rel="stylesheet" href="https://fonts.googleapis.com/css2?family=Barlow+Condensed:ital,wght@0,700;1,700;1,800&family=Roboto:wght@400;500;700&display=swap">
<style>
:root{
  --green:#8ea31c;
  --green-dark:#7a8d14;
  --olive-light:#c4c98f;
  --cream:#f2f3ec;
  --ink:#1c1c1a;
  --text:#3a3a3a;
  --muted:#6d6d6d;
  --footer:#1f1f1d;
  --white:#ffffff;
}
*{box-sizing:border-box;margin:0;padding:0}
html,body{width:1200px;height:4276px;overflow:hidden}
body{font-family:"Roboto",Arial,sans-serif;color:var(--text);background:var(--white);position:relative}
.abs{position:absolute}
.heading{font-family:"Barlow Condensed","Arial Narrow",sans-serif;font-style:italic;font-weight:800;color:var(--ink);text-transform:uppercase;letter-spacing:.5px}
.btn{position:absolute;display:flex;align-items:center;justify-content:center;gap:10px;background:var(--green);color:#fff;font-weight:700;font-size:15px;text-transform:uppercase;border-radius:3px}
.btn svg{width:15px;height:15px}
section{position:absolute;left:0;width:1200px}

/* header */
.site-header{top:0;height:100px;background:#fff}
.brand{position:absolute;left:110px;top:26px;display:flex;align-items:center;gap:12px}
.brand-square{width:30px;height:30px;background:var(--green)}
.brand-name{font-family:"Barlow Condensed",sans-serif;font-weight:700;font-size:40px;color:var(--ink);line-height:1}
.search{position:absolute;left:488px;top:28px;width:297px;height:42px;border:1px solid #cfcfcf;border-radius:3px;font-size:15px;color:#666;padding:12px 18px}
.search svg{position:absolute;right:14px;top:12px;width:16px;height:16px}
.btn-request{left:800px;top:29px;width:160px;height:40px;background:var(--olive-light);text-transform:none;font-weight:500}
.btn-sign{left:978px;top:29px;width:111px;height:40px}

.main-nav{top:100px;height:54px;background:var(--green)}
.nav-links{position:absolute;left:111px;top:0;height:54px;display:flex;align-items:center;font-size:13.5px;color:#fff;text-transform:uppercase}
.nav-links span.sep{margin:0 26px}
.socials{position:absolute;display:flex;gap:8px}
.socials i{display:block;width:32px;height:32px;border:1.5px solid #fff;border-radius:50%}
.main-nav .socials{left:936px;top:11px}

/* hero */
.hero{top:154px;height:634px;background:linear-gradient(90deg,#141a1c 0%,#2d3438 40%,#6b6258 70%,#9a8f80 100%)}
.hero h1{position:absolute;left:110px;top:180px;font-size:62px;line-height:60px;color:#fff}
.hero p{position:absolute;left:110px;top:325px;width:420px;color:#fff;font-size:14.5px;line-height:25px}
.hero .btn{left:110px;top:399px;width:170px;height:45px}

/* about */
.about{top:788px;height:595px;background:linear-gradient(90deg,#fff 40%,#f3f4f2 100%)}
.about-frame{position:absolute;left:155px;top:92px;width:366px;height:400px;border:2.5px solid var(--green)}
.photo{position:absolute}
.about h2{position:absolute;left:617px;top:120px;font-size:37px}
.about p{position:absolute;left:617px;top:168px;width:470px;font-size:14.5px;line-height:25.6px;text-align:justify;color:#444}
.about .btn{left:617px;top:450px;width:171px;height:47px}

/* why */
.why{top:1383px;height:614px;background:var(--cream)}
.why h2{position:absolute;left:110px;top:70px;font-size:37px}
.why-item{position:absolute;left:110px;width:470px;height:100px}
.why-item svg{position:absolute;left:0;top:18px;width:72px;height:66px}
.why-item h3{position:absolute;left:88px;top:0;font-size:17px;font-weight:700;color:var(--ink)}
.why-item p{position:absolute;left:88px;top:36px;width:385px;font-size:14.5px;line-height:26px;color:#444}

/* services */
.services{top:1997px;height:609px;background:#fff}
.section-title{position:absolute;left:0;width:1200px;text-align:center;font-size:37px}
.card{position:absolute;top:154px;width:279px;height:369px;background:#fff;box-shadow:0 4px 18px rgba(0,0,0,.12)}
.card .photo{left:9px;top:7px;width:261px;height:176px}
.card h3{position:absolute;left:23px;top:210px;font-size:14px;font-weight:700;font-style:italic;color:var(--ink);text-transform:uppercase}
.card p{position:absolute;left:23px;top:241px;width:240px;font-size:14.5px;line-height:25.5px;color:#777}
.card .more{position:absolute;left:23px;top:332px;display:flex;align-items:center;gap:10px;color:var(--green);font-weight:700;font-size:14.5px}
.card .more svg{width:15px;height:15px}

/* categories */
.categories{top:2606px;height:448px;background:linear-gradient(180deg,#93a71f,#8a9e19)}
.categories .section-title{color:#fff;top:65px}
.cat{position:absolute;top:167px;width:166px;text-align:center}
.cat .ring{width:166px;height:166px;border-radius:50%;border:4px solid #fff;box-shadow:0 0 0 3px #d7e27a inset}
.cat span{display:block;margin-top:24px;font-weight:700;color:#fff;font-size:15.5px;text-transform:uppercase}

/* testimonials */
.testimonials{top:3054px;height:445px;background:#fff}
.review{position:absolute;top:158px;width:314px;height:199px;background:#fff;box-shadow:0 3px 16px rgba(0,0,0,.1)}
.avatar{position:absolute;left:26px;top:26px;width:64px;height:64px;border-radius:50%;border:3px solid var(--green)}
.stars{position:absolute;left:108px;top:34px;color:var(--green);font-size:13px;letter-spacing:2px}
.review h4{position:absolute;left:108px;top:58px;font-size:13px;font-style:italic;font-weight:700;color:var(--ink)}
.review p{position:absolute;left:29px;top:102px;width:262px;font-size:14.5px;line-height:25.5px;color:#666}

/* brands */
.brands{top:3499px;height:365px;background:linear-gradient(180deg,#c9cd98,#bcc284)}
.brands .section-title{top:72px;color:#fff}
.brands p{position:absolute;left:210px;top:126px;width:780px;text-align:center;color:#fff;font-size:14.5px;line-height:26px}
.brand-box{position:absolute;top:216px;width:178px;height:80px;border:2px solid #fff;border-radius:3px;display:flex;align-items:center;justify-content:center;gap:10px;color:#fff;font-size:32px;font-weight:500}
.brand-box i{display:block;width:26px;height:26px;border-radius:50%;border:4px solid #fff}

/* footer */
.site-footer{top:3864px;height:412px;background:var(--footer);color:#fff}
.footer-brand{position:absolute;left:110px;top:96px;display:flex;align-items:center;gap:12px}
.footer-brand .brand-name{color:#fff;font-size:38px}
.site-footer .socials{left:122px;top:194px;gap:10px}
.site-footer .socials i{width:36px;height:36px;border:none;background:var(--olive-light)}
.fcol{position:absolute;top:100px}
.fcol h5{font-size:16px;font-weight:700;margin-bottom:22px}
.fcol ul{list-style:none}
.fcol li{font-size:13.5px;height:34px;display:flex;gap:18px}
.fcol li::before{content:"»";color:#ccc}
.addr{position:absolute;left:845px;top:100px;width:245px}
.addr h5{font-size:16px;font-weight:700;margin-bottom:26px}
.addr .row{position:relative;padding-left:26px;margin-bottom:20px;font-size:13px;line-height:18px}
.addr .row b{display:block;font-size:12px}
.addr svg{position:absolute;left:0;top:2px;width:14px;height:14px}
.footer-rule{position:absolute;left:110px;top:354px;width:977px;height:1px;background:#4a4a46}
.copy{position:absolute;left:0;top:378px;width:1200px;text-align:center;font-size:13.5px}
</style>
</head>
<body>

<header class="site-header abs" style="left:0;width:1200px">
  <div class="brand"><span class="brand-square"></span><span class="brand-name">NORTHLINE</span></div>
  <div class="search">Search
    <svg viewBox="0 0 16 16"><circle cx="6.5" cy="6.5" r="5" fill="none" stroke="#222" stroke-width="2"/><line x1="10" y1="10" x2="15" y2="15" stroke="#222" stroke-width="2"/></svg>
  </div>
  <a class="btn btn-request">Request Account</a>
  <a class="btn btn-sign">Sign In</a>
</header>

<nav class="main-nav abs" style="left:0;width:1200px">
  <div class="nav-links">
    <span>Home</span><span class="sep">|</span><span>About Us</span><span class="sep">|</span><span>Service</span><span class="sep">|</span><span>Testimonials</span><span class="sep">|</span><span>HVAC Distribution</span><span class="sep">|</span><span>Contact Us</span>
  </div>
  <div class="socials"><i aria-label="Social link 1"></i><i aria-label="Social link 2"></i><i aria-label="Social link 3"></i><i aria-label="Social link 4"></i></div>
</nav>

<section class="hero" role="img" aria-label="Warehouse staff checking a parts box on a tablet between storage shelves">
  <h1 class="heading">Northline HVAC<br>Distribution</h1>
  <p>Lorem ipsum dolor sit amet consectetur adipiscing elit sed eiusmod tempor incididunt labore et dolore magna aliqua.</p>
  <a class="btn">Get Started <svg viewBox="0 0 16 16"><circle cx="8" cy="8" r="8" fill="#fff"/><path d="M6 4.5 9.5 8 6 11.5" stroke="#8ea31c" stroke-width="2" fill="none"/></svg></a>
</section>

<section class="about">
  <div class="about-frame"></div>
  <div class="photo" role="img" aria-label="Delivery workers unloading a parts box from a truck" style="left:111px;top:110px;width:388px;height:360px;background:linear-gradient(135deg,#5a6a3a,#c08a4a 45%,#2f4f8a 70%,#3e6a30)"></div>
  <div class="photo" role="img" aria-label="Customer receiving a parts package" style="left:332px;top:301px;width:221px;height:206px;border:6px solid #fff;background:linear-gradient(135deg,#2c3a4a,#9a8a78 55%,#d8c6b0)"></div>
  <h2 class="heading">About Us</h2>
  <p>Lorem ipsum dolor sit amet, consectetur adipiscing elit, sed do eiusmod tempor incididunt ut labore et dolore magna aliqua. Ut enim ad minim veniam, quis nostrud exercitation ullamco laboris nisi ut aliquip ex ea commodo consequat. Duis aute irure dolor in reprehenderit in voluptate velit esse cillum dolore eu fugiat nulla pariatur.Lorem ipsum dolor sit amet, consectetur adipiscing elit, sed do eiusmod tempor incididunt ut labore et dolore magna aliqua. Ut enim ad minim veniam, quis nostrud exercitation ullamco laboris nisi ut aliquip ex ea commodo consequat. Duis aute irure dolor in reprehenderit in voluptate velit esse cillum dolore eu.</p>
  <a class="btn">Learn More <svg viewBox="0 0 16 16"><circle cx="8" cy="8" r="8" fill="#fff"/><path d="M6 4.5 9.5 8 6 11.5" stroke="#8ea31c" stroke-width="2" fill="none"/></svg></a>
</section>

<section class="why">
  <h2 class="heading">Why Choose Us</h2>
  <div class="why-item" style="top:144px">
    <svg viewBox="0 0 72 66" fill="none" stroke="#8ea31c" stroke-width="2.5"><rect x="14" y="6" width="54" height="24" rx="3"/><line x1="20" y1="22" x2="62" y2="22"/><circle cx="18" cy="46" r="12"/><path d="M18 38v16M10 46h16"/></svg>
    <h3>Lorem ipsum dolor</h3>
    <p>Lorem ipsum dolor sit amet consectetur adipiscing elit, sed do eiusmod tempor incididunt ut labored.</p>
  </div>
  <div class="why-item" style="top:252px">
    <svg viewBox="0 0 72 66" fill="none" stroke="#8ea31c" stroke-width="2.5"><rect x="6" y="16" width="38" height="30"/><path d="M44 24h14l10 12v10H44z"/><circle cx="18" cy="50" r="6"/><circle cx="56" cy="50" r="6"/></svg>
    <h3>Lorem ipsum dolor</h3>
    <p>Lorem ipsum dolor sit amet consectetur adipiscing elit, sed do eiusmod tempor incididunt ut labored.</p>
  </div>
  <div class="why-item" style="top:361px">
    <svg viewBox="0 0 72 66" fill="none" stroke="#8ea31c" stroke-width="2.5"><circle cx="28" cy="34" r="24"/><path d="M18 28l10-6 10 6v12l-10 6-10-6z M18 28l10 6 10-6 M28 34v12"/></svg>
    <h3>Lorem ipsum dolor</h3>
    <p>Lorem ipsum dolor sit amet consectetur adipiscing elit, sed do eiusmod tempor incididunt ut labored.</p>
  </div>
  <div class="why-item" style="top:470px">
    <svg viewBox="0 0 72 66" fill="none" stroke="#8ea31c" stroke-width="2.5"><path d="M8 26l24-10 24 10v24l-24 12-24-12z M8 26l24 12 24-12 M32 38v24"/><circle cx="32" cy="10" r="7"/><path d="M29 10l2 2 4-4"/></svg>
    <h3>Lorem ipsum dolor</h3>
    <p>Lorem ipsum dolor sit amet consectetur adipiscing elit, sed do eiusmod tempor incididunt ut labored.</p>
  </div>
  <div class="photo" role="img" aria-label="Warehouse worker carrying a parts box" style="left:672px;top:69px;width:424px;height:424px;border-radius:50%;background:linear-gradient(135deg,#e9e2d6,#c7a57a 50%,#2b4a8a)"></div>
  <div class="photo" role="img" aria-label="Hands passing a parts package" style="left:659px;top:338px;width:210px;height:210px;border-radius:50%;border:3px solid #fff;box-shadow:0 6px 18px rgba(0,0,0,.2);background:radial-gradient(circle,#d9a264,#e7ded2 75%)"></div>
</section>

<section class="services">
  <h2 class="heading section-title" style="top:80px">Our Services</h2>
  <div class="card" style="left:138px">
    <div class="photo" role="img" aria-label="Wall-mounted air conditioner" style="background:linear-gradient(180deg,#eef0ef,#c9cfcf)"></div>
    <h3>Lorem ipsum dolor sit</h3>
    <p>Lorem ipsum dolor sit consectetur adipiscing elited sed do eiusmod tempor incididunt labore dolore.</p>
    <span class="more">Read More <svg viewBox="0 0 16 16"><circle cx="8" cy="8" r="8" fill="#8ea31c"/><path d="M6 4.5 9.5 8 6 11.5" stroke="#fff" stroke-width="2" fill="none"/></svg></span>
  </div>
  <div class="card" style="left:461px">
    <div class="photo" role="img" aria-label="Warehouse staff checking stock boxes" style="background:linear-gradient(160deg,#e3e5e3,#c6a77c 60%,#7c8a8e)"></div>
    <h3>Lorem ipsum dolor sit</h3>
    <p>Lorem ipsum dolor sit consectetur adipiscing elited sed do eiusmod tempor incididunt labore dolore.</p>
    <span class="more">Read More <svg viewBox="0 0 16 16"><circle cx="8" cy="8" r="8" fill="#8ea31c"/><path d="M6 4.5 9.5 8 6 11.5" stroke="#fff" stroke-width="2" fill="none"/></svg></span>
  </div>
  <div class="card" style="left:785px">
    <div class="photo" role="img" aria-label="Technician fitting copper pipes" style="background:linear-gradient(135deg,#3a2c24,#c07a48 50%,#e8b48a)"></div>
    <h3>Lorem ipsum dolor sit</h3>
    <p>Lorem ipsum dolor sit consectetur adipiscing elited sed do eiusmod tempor incididunt labore dolore.</p>
    <span class="more">Read More <svg viewBox="0 0 16 16"><circle cx="8" cy="8" r="8" fill="#8ea31c"/><path d="M6 4.5 9.5 8 6 11.5" stroke="#fff" stroke-width="2" fill="none"/></svg></span>
  </div>
</section>

<section class="categories">
  <h2 class="heading section-title">Our Categories</h2>
  <div class="cat" style="left:105px"><div class="ring" role="img" aria-label="Plumbing pipe repair" style="background:linear-gradient(135deg,#dfe6ea,#8e9aa2)"></div><span>Plumbing</span></div>
  <div class="cat" style="left:310px"><div class="ring" role="img" aria-label="Oil radiator heater" style="background:linear-gradient(135deg,#f4f4f2,#c4c6c2)"></div><span>Heater</span></div>
  <div class="cat" style="left:520px"><div class="ring" role="img" aria-label="Row of outdoor HVAC units" style="background:linear-gradient(135deg,#e5e9ec,#9aa3a8)"></div><span>HVAC</span></div>
  <div class="cat" style="left:725px"><div class="ring" role="img" aria-label="Pipe fittings and valves" style="background:linear-gradient(135deg,#b8bcbf,#5d6468)"></div><span>Fittings</span></div>
  <div class="cat" style="left:931px"><div class="ring" role="img" aria-label="Electrician testing a panel" style="background:linear-gradient(135deg,#3b3f46,#c2522e 55%,#2b2f36)"></div><span>Electrical</span></div>
</section>

<section class="testimonials">
  <h2 class="heading section-title" style="top:80px">What Customers Say</h2>
  <div class="review" style="left:110px">
    <div class="avatar" role="img" aria-label="Customer portrait" style="background:#c9b7a2"></div>
    <div class="stars">★★★★★</div><h4>JONE DEO</h4>
    <p>Lorem ipsum dolor sit consectetured adipiscing elited sed doe eiusmoded tempor incididunt labore et dolore.</p>
  </div>
  <div class="review" style="left:443px">
    <div class="avatar" role="img" aria-label="Customer portrait" style="background:#a8b7c8"></div>
    <div class="stars">★★★★★</div><h4>JONE DEO</h4>
    <p>Lorem ipsum dolor sit consectetured adipiscing elited sed doe eiusmoded tempor incididunt labore et dolore.</p>
  </div>
  <div class="review" style="left:777px">
    <div class="avatar" role="img" aria-label="Customer portrait" style="background:#b9c2cc"></div>
    <div class="stars">★★★★★</div><h4>JONE DEO</h4>
    <p>Lorem ipsum dolor sit consectetured adipiscing elited sed doe eiusmoded tempor incididunt labore et dolore.</p>
  </div>
</section>

<section class="brands">
  <h2 class="heading section-title">Trusted Brands</h2>
  <p>Lorem ipsum dolor sit amet, consectetur adipiscing elit, sed do eiusmod tempor incididunt ut labore et dolore magna aliqua. Ut enim ad minim veniam, quis nostrud exercitation ullamco labo</p>
  <div class="brand-box" style="left:134px"><i></i>Corvia</div>
  <div class="brand-box" style="left:323px"><i></i>Tenvar</div>
  <div class="brand-box" style="left:512px"><i></i>Idello</div>
  <div class="brand-box" style="left:701px"><i></i>Lumen</div>
  <div class="brand-box" style="left:889px"><i></i>Castra</div>
</section>

<footer class="site-footer abs" style="left:0;width:1200px">
  <div class="footer-brand"><span class="brand-square"></span><span class="brand-name">NORTHLINE</span></div>
  <div class="socials"><i aria-label="Social link 1"></i><i aria-label="Social link 2"></i><i aria-label="Social link 3"></i><i aria-label="Social link 4"></i></div>
  <div class="fcol" style="left:393px"><h5>Quick Links</h5>
    <ul><li>Home</li><li>About Us</li><li>Services</li><li>Testimonials</li><li>Contact Us</li></ul></div>
  <div class="fcol" style="left:614px"><h5>Other Links</h5>
    <ul><li>Support</li><li>Terms &amp; Condition</li><li>Contact Us</li><li>Privacy Policy</li><li>FAQ</li><li>Site Map</li></ul></div>
  <div class="addr"><h5>Address</h5>
    <div class="row"><svg viewBox="0 0 14 14"><path d="M3 1l3 3-2 2c1 2 2 3 4 4l2-2 3 3-2 2C6 13 1 8 1 3z" fill="#8ea31c"/></svg><b>Phone</b>+1 555 010 2040</div>
    <div class="row"><svg viewBox="0 0 14 14"><rect x="1" y="3" width="12" height="8" fill="#8ea31c"/><path d="M1 3l6 5 6-5" stroke="#1f1f1d" fill="none"/></svg><b>Email</b>info@northlinehvac.example</div>
    <div class="row"><svg viewBox="0 0 14 14"><path d="M7 1a4.5 4.5 0 0 1 4.5 4.5C11.5 9 7 13 7 13S2.5 9 2.5 5.5A4.5 4.5 0 0 1 7 1z" fill="#8ea31c"/><circle cx="7" cy="5.5" r="1.6" fill="#1f1f1d"/></svg><b>Location</b>410 Lorem ipsum dolor perspiciatis accusantium doloremque</div>
  </div>
  <div class="footer-rule"></div>
  <div class="copy">© 2023 Northline HVAC Distribution. &nbsp;| All Rights Reserved |</div>
</footer>

</body>
</html>
```